Stylish Business Cards Wanted

- DOUBLE SIDED Design Required -

High end, edgy cards for a corporate and personal stylist. Must include logo,
Name: Belinda Harwick
Title: Director and Stylist
telephone : +61 8 7142 5809
email: belinda@theloombriefing.example
website: theloombriefing.example
Tag: Corporate Workwear & Uniform Specialist | Personal Stylist
Would like nice icons for telephone, email, website

Target Market(s)

Businesses wanting stylish uniforms, people wanting stylish wardrobes

Industry/Entity Type

Corporate Workwear Stylist

Contact Information for Business Card

I would like black, white and gold foiling incorporated in the design - possibly a touch of the other colours on my branding guide attached Name: Belinda Harwick Title: Director and Stylist telephone : +61 8 7142 5809 email: belinda@theloombriefing.example website: theloombriefing.example Tag: Corporate Workwear & Uniform Specialist | Personal Stylist Would like nice icons for telephone, email, website

Font styles to use
Other font styles liked:
• Raleway

Colors

Designer to choose colors to be used in the design.

Requirements
Must have
• Gold foil accents

```html
<!DOCTYPE html>
<html lang="en">
<head>
<meta charset="utf-8">
<title>The Loom Briefing – Business Cards</title>
<link rel="stylesheet" href="https://fonts.googleapis.com/css2?family=Raleway:wght@400;500;700&display=swap">
<style>
  :root {
    --stage: #ececec;
    --ink: #000000;
    --gold: #e3bc58;
    --text-dark: #231f20;
  }
  * { margin: 0; padding: 0; box-sizing: border-box; }
  html, body {
    width: 1200px; height: 507px; overflow: hidden;
    background: var(--stage);
    font-family: "Raleway", Arial, sans-serif;
  }
  .stage { position: relative; width: 1200px; height: 507px; }

  .card {
    position: absolute; top: 106px;
    width: 493px; height: 295px;
  }
  .card--front { left: 83px; background: var(--ink); }
  .card--back { left: 624px; background: var(--gold); }

  .brand-name {
    position: absolute;
    font-weight: 700;
    text-align: center;
    line-height: 1.05;
    letter-spacing: 0.02em;
  }
  .card--front .brand-name {
    left: 0; right: 0; top: 78px;
    font-size: 40px; color: var(--gold);
  }
  .card--back .brand-name {
    left: 40px; width: 150px; top: 112px;
    font-size: 28px; color: var(--text-dark);
  }

  .tagline {
    position: absolute; left: 76px; top: 203px;
    width: 341px; height: 24px;
    border: 1px solid var(--gold); border-radius: 7px;
    color: var(--gold);
    font-size: 12px; font-weight: 400;
    display: flex; align-items: center; justify-content: center; gap: 6px;
    white-space: nowrap;
  }

  .divider {
    position: absolute; left: 197px; top: 92px;
    width: 1px; height: 110px; background: var(--text-dark);
  }
  .contact { position: absolute; left: 210px; top: 98px; color: var(--text-dark); }
  .contact__name { font-size: 22px; font-weight: 700; line-height: 1.1; }
  .contact__title { font-size: 11px; margin-top: 1px; }
  .contact__list { list-style: none; margin-top: 7px; }
  .contact__item {
    display: flex; align-items: center; gap: 6px;
    font-size: 14px; height: 21.5px; white-space: nowrap;
  }
  .contact__icon { width: 11px; height: 11px; flex: none; }
</style>
</head>
<body>
<main class="stage">
  <section class="card card--front" aria-label="Card front">
    <p class="brand-name">The Loom<br>Briefing</p>
    <p class="tagline">
      <span>Corporate Workwear</span><span>|</span>
      <span>Uniform Specialist</span><span>|</span>
      <span>Personal Stylist</span>
    </p>
  </section>

  <section class="card card--back" aria-label="Card back">
    <p class="brand-name">The Loom<br>Briefing</p>
    <div class="divider"></div>
    <div class="contact">
      <h1 class="contact__name">Belinda Harwick</h1>
      <p class="contact__title">Director and Stylist</p>
      <ul class="contact__list">
        <li class="contact__item">
          <svg class="contact__icon" viewBox="0 0 12 12" aria-hidden="true">
            <circle cx="6" cy="6" r="6" fill="#231f20"/>
            <path d="M3 5.2c0-1 1.3-1.6 3-1.6s3 .6 3 1.6H7.6v-.8H4.4v.8z M3.6 8.6l1-2.6h2.8l1 2.6z" fill="#e3bc58"/>
          </svg>
          <span>+61 8 7142 5809</span>
        </li>
        <li class="contact__item">
          <svg class="contact__icon" viewBox="0 0 12 12" aria-hidden="true">
            <circle cx="6" cy="6" r="6" fill="#231f20"/>
            <rect x="3" y="4" width="6" height="4.2" fill="#e3bc58"/>
            <path d="M3 4l3 2.3L9 4" fill="none" stroke="#231f20" stroke-width="0.7"/>
          </svg>
          <span>belinda@theloombriefing.example</span>
        </li>
        <li class="contact__item">
          <svg class="contact__icon" viewBox="0 0 12 12" aria-hidden="true">
            <circle cx="6" cy="6" r="6" fill="#231f20"/>
            <g fill="none" stroke="#e3bc58" stroke-width="0.7">
              <circle cx="6" cy="6" r="3.4"/>
              <ellipse cx="6" cy="6" rx="1.4" ry="3.4"/>
              <path d="M2.6 6h6.8M3.1 4.3h5.8M3.1 7.7h5.8"/>
            </g>
          </svg>
          <span>theloombriefing.example</span>
        </li>
      </ul>
    </div>
  </section>
</main>
</body>
</html>
```